Health Coaching website focused on diabetes management using Vantelo template

I am starting a health coaching business and would like to use Plumestack and an Vantelo template. The coaching will focus on Pre-diabetic and chronic disease patients so it will need to have a personal as well as a slight clinical look to it. The site should have an overall look similar to Meadow Loop theme. I will purchase the Vantelo designer package for use.

Target Market(s)

40-60 year olds with pre-diabetes or concerned about chronic disease, maintaining health, nutrition and weight loss

Industry/Entity Type

Health And Wellness

Number of Pages Required

5+ page

Colors
87cfc6
60b9df
fee18a
00a990
3276b5

Requirements
Must have
• It should contain an ecommerce tab, member's only area, interactive blog, built-in SEO and an opt-in area on every page. It should have several call to actions throughout the site. The site should have an overall look similar to Meadow Loop theme. Hosting on Servunda. Also needed all the essential plumestack plugins:
• Keystep forms & Keystep entry pages
• Pondra Metrics
• Vantelo shield plus
• Postwren
• Valdeno
• Vault Parrot
• Kindle SEO
• Drifting Share Strip
• Q7 Rapid Store
• Tembi
Nice to have
• Ecommerce ready with cartoflex plugin
• Hi-res pictures of people in my demographic enjoying life and/or exercising, cooking, etc.
Should not have
• slider on homepage
• my profile on homepage

```html
<!DOCTYPE html>
<html lang="en">
<head>
<meta charset="utf-8">
<title>VitaPath For Wellness – Blog</title>
<link href="https://fonts.googleapis.com/css2?family=Jost:wght@400;500&family=Open+Sans:ital,wght@0,400;0,600;0,700;1,400&display=swap" rel="stylesheet">
<style>
:root{
  --blue:#3276b5;
  --teal:#00a990;
  --teal-soft:#87cfc6;
  --sky:#60b9df;
  --sun:#fee18a;
  --ink:#333;
  --text:#555;
  --muted:#888;
  --line:#e2e2e2;
  --crumb:#e8e8e8;
  --footer:#1e2430;
  --cream:#f2efe6;
}
*{box-sizing:border-box;margin:0;padding:0}
html,body{width:1200px;height:2624px;overflow:hidden}
body{position:relative;background:#fff;font-family:"Open Sans",Arial,sans-serif;color:var(--text)}
a{color:inherit;text-decoration:none}
.abs{position:absolute}

/* header */
.site-header{left:0;top:0;width:1200px;height:114px}
.brand{left:163px;top:22px;display:flex;align-items:center;gap:14px}
.brand-mark{width:60px;height:60px;border-radius:50%;background:var(--teal-soft)}
.brand-name{font-family:"Jost",sans-serif;font-size:31px;line-height:33px;color:#222;font-weight:400}
.header-phone{left:624px;top:40px;display:flex;align-items:center;gap:14px;font-size:22px;color:#333}
.phone-dot{width:36px;height:36px;border-radius:50%;background:var(--teal);display:flex;align-items:center;justify-content:center}
.appt-btn{left:821px;top:40px;width:218px;height:38px;background:var(--teal);color:#fff;font-size:13px;font-weight:600;display:flex;align-items:center;justify-content:center;gap:10px;text-transform:uppercase;letter-spacing:.2px}

/* nav */
.main-nav{left:0;top:114px;width:1200px;height:37px;background:var(--blue)}
.main-nav ul{list-style:none;display:flex;position:absolute;left:163px;top:0;height:37px;border-left:1px solid rgba(255,255,255,.15)}
.main-nav li{height:37px;display:flex;align-items:center;padding:0 18px;color:#fff;font-size:12.5px;font-weight:700;text-transform:uppercase;border-right:1px solid rgba(255,255,255,.15)}
.main-nav li.active{background:var(--teal)}

/* hero */
.hero{left:0;top:151px;width:1200px;height:337px;background:linear-gradient(90deg,#b25a34 0%,#8a6a52 18%,#9a9080 38%,#d8d2c2 56%,var(--cream) 66%,var(--cream) 100%)}
.hero-text{left:640px;top:60px;width:440px;text-align:center;color:#111}
.hero-text h1{font-family:"Jost",sans-serif;font-weight:400;font-size:50px;line-height:60px}
.hero-text p{font-size:20px;line-height:25px;margin-top:10px}
.hero-dots{left:830px;top:266px;display:flex;gap:6px}
.hero-dots span{width:10px;height:10px;border-radius:50%;background:#777}
.hero-dots span.on{background:var(--teal)}

.breadcrumb{left:0;top:488px;width:1200px;height:37px;background:var(--crumb);font-size:13px;color:#333;padding:11px 0 0 162px}
.breadcrumb b{font-weight:700}

/* section title */
.section-title{left:0;top:560px;width:1200px;text-align:center;font-family:"Jost",sans-serif;font-weight:400;font-size:30px;color:#222}
.section-title em{font-style:normal;color:var(--blue)}
.title-rule{left:366px;top:626px;width:468px;height:1px;background:#bbb}
.title-rule span{position:absolute;left:222px;top:-12px;width:24px;height:24px;border-radius:50%;background:#fff;border:1px solid #bbb}

/* posts */
.post{left:161px;width:598px;height:460px;border:1px solid var(--line);background:#fff}
.post-media{height:229px}
.post-body{padding:22px 18px 0}
.post-title{font-size:16px;font-weight:600;color:var(--blue)}
.post-meta{display:flex;justify-content:space-between;margin-top:12px;font-size:11px;font-style:italic;color:var(--muted)}
.post-comments{font-style:normal;font-weight:700;color:#333;font-size:13px;display:flex;align-items:center;gap:6px}
.post-excerpt{margin-top:16px;font-size:13px;line-height:21px;color:#555}
.post-actions{display:flex;align-items:center;gap:14px;margin-top:14px}
.read-more{width:114px;height:32px;background:var(--teal);color:#fff;font-size:13px;display:flex;align-items:center;justify-content:center;text-transform:uppercase}
.share{font-size:11px;color:#333}

/* pagination */
.pagination{left:262px;top:2155px;display:flex;align-items:center;gap:8px;font-size:11px;color:#333}
.pg-btn{width:98px;height:28px;border:1px solid #ccc;border-radius:14px;display:flex;align-items:center;justify-content:center;font-weight:600;text-transform:uppercase;gap:4px}
.pg-num{width:27px;height:27px;border:1px solid #bbb;border-radius:50%;display:flex;align-items:center;justify-content:center}
.pg-num.on{border:2px solid var(--teal);color:var(--teal)}
.pg-gap{width:18px}

/* sidebar */
.search-box{left:791px;top:679px;width:247px;height:39px;border:1px solid #ccc;font-size:11px;color:#333;padding:12px 10px}
.search-box svg{position:absolute;right:10px;top:12px}
.widget{left:791px;width:247px;border:1px solid var(--line);background:#fff}
.widget h3{height:40px;background:var(--blue);color:#fff;font-weight:400;font-size:15px;text-transform:uppercase;padding:11px 13px 0}
.widget ul{list-style:none;padding:4px 14px 0}
.widget li{height:37px;border-bottom:1px solid var(--line);display:flex;align-items:center;gap:9px;font-size:12px;color:#333}
.widget li:last-child{border-bottom:0}
.recent{display:flex;gap:10px;padding:0 0 0 8px;height:85px;align-items:center;border-bottom:1px solid var(--line)}
.recent:last-child{border-bottom:0}
.recent-thumb{width:62px;height:56px;flex:none}
.recent b{display:block;font-size:11.5px;color:#222}
.recent small{display:block;font-size:9.5px;color:var(--muted);margin:4px 0}
.recent span{font-size:13px;color:#333;display:flex;gap:5px;align-items:center}
.tags{padding:12px 16px;font-size:11.5px;line-height:22px;color:#333;text-align:justify;word-spacing:6px}
.tags b{color:var(--teal);font-weight:600}

/* footer */
.site-footer{left:0;top:2298px;width:1200px;height:280px;background:var(--footer);color:#ccc}
.f-col{top:42px}
.f-col h4{font-family:"Jost",sans-serif;font-weight:400;font-size:18px;color:#fff;text-transform:uppercase;padding-bottom:14px;border-bottom:1px solid #3a4150;margin-bottom:12px}
.f-col h4 em{font-style:normal;color:var(--teal)}
.quick ul{list-style:none}
.quick li{font-size:12px;line-height:20px}
.quick li::before{content:"› ";color:var(--teal)}
.quick li.on{color:var(--teal)}
.contact p{font-size:12px;line-height:18px}
.contact .firm{color:#fff;font-weight:600;text-transform:uppercase}
.contact .row{display:flex;align-items:center;gap:10px;font-size:15px;margin-top:10px;color:#ddd}
.contact .row.small{font-size:12px;margin-top:14px}
.follow ul{list-style:none}
.follow li{display:flex;align-items:center;gap:12px;font-size:12px;height:39px}
.follow li i{width:30px;height:30px;border-radius:50%;border:2px solid #fff}
.footer-brand{left:860px;top:94px;width:180px;text-align:center;font-family:"Jost",sans-serif;font-size:22px;color:#8c93a0}
.footer-brand span{display:block;width:70px;height:70px;border-radius:50%;background:#4a5160;margin:0 auto 14px}
.copyright{left:0;top:2578px;width:1200px;height:46px;background:var(--teal);color:#fff;font-size:12px;padding:15px 0 0 162px}
</style>
</head>
<body>

<header class="site-header abs">
  <div class="brand abs"><span class="brand-mark"></span><span class="brand-name">VitaPath<br>For Wellness</span></div>
  <div class="header-phone abs">
    <span class="phone-dot"><svg width="16" height="16" viewBox="0 0 24 24"><path fill="#fff" d="M6.6 10.8a15 15 0 0 0 6.6 6.6l2.2-2.2c.3-.3.7-.4 1-.2 1.1.4 2.3.6 3.6.6.6 0 1 .4 1 1V20c0 .6-.4 1-1 1A17 17 0 0 1 3 4c0-.6.4-1 1-1h3.5c.6 0 1 .4 1 1 0 1.3.2 2.5.6 3.6.1.3 0 .7-.2 1z"/></svg></span>
    555-310-2847
  </div>
  <a class="appt-btn abs" href="#"><svg width="15" height="15" viewBox="0 0 16 16"><rect x="1.5" y="3" width="13" height="11.5" fill="none" stroke="#fff" stroke-width="1.4"/><path d="M1.5 6.5h13M5 1v3M11 1v3" stroke="#fff" stroke-width="1.4"/></svg>Make an Appointment</a>
</header>

<nav class="main-nav abs">
  <ul>
    <li>Home</li><li>About VitaPath</li><li>Our Courses</li><li>Special Offers</li><li>Testimonials</li><li class="active">Blog</li><li>Faq's</li><li>Contact Us</li>
  </ul>
</nav>

<section class="hero abs" role="img" aria-label="Photo of a smiling couple cooking fresh vegetables together in a bright kitchen">
  <div class="hero-text abs">
    <h1>VitaPath<br>For Wellness</h1>
    <p>Get the health and lifestyle<br>you want now!</p>
  </div>
  <div class="hero-dots abs"><span class="on"></span><span></span><span></span><span></span></div>
</section>

<div class="breadcrumb abs">Home / <b>Blog</b></div>

<h2 class="section-title abs">Latest <em>Blog</em></h2>
<div class="title-rule abs"><span></span></div>

<article class="post abs" style="top:679px">
  <div class="post-media" role="img" aria-label="Photo of a couple tasting food together while cooking at home" style="background:linear-gradient(90deg,#c99b6a,#e8d2b0 45%,#b07850 80%,#d9b58a)"></div>
  <div class="post-body">
    <h3 class="post-title">On the other hand, we denounce with righteous</h3>
    <div class="post-meta"><span>21 Sep 2016 - Posted by Admin</span><span class="post-comments"><svg width="14" height="12" viewBox="0 0 14 12"><path d="M1 1h8v6H4l-3 2z" fill="none" stroke="#00a990" stroke-width="1.3"/><path d="M10 4h3v6l-2-1.5H6V8" fill="none" stroke="#00a990" stroke-width="1.3"/></svg>05</span></div>
    <p class="post-excerpt">Sed ut perspiciatis unde omnis iste natus error sit voluptatem accusantium doloremque laudantium, totam rem aperiam, eaque ipsa quae ab illo inventore veritatis et quasi architecto beatae vitae dicta sunt explicabo. Nemo enim ipsam voluptatem quia voluptas sit aspernatur aut odit aut fugit, sed quia consequuntur magni dolores eos qui sequi nesciunt.</p>
    <div class="post-actions"><a class="read-more" href="#">Read More</a><span class="share">&lt; Share It</span></div>
  </div>
</article>

<article class="post abs" style="top:1170px">
  <div class="post-media" role="img" aria-label="Photo of a smiling mature couple in a light kitchen with fresh greens" style="background:linear-gradient(90deg,#cfe3ec,#eef5f7 40%,#f3efc8 70%,#e8f0f2)"></div>
  <div class="post-body">
    <h3 class="post-title">On the other hand, we denounce with righteous</h3>
    <div class="post-meta"><span>21 Sep 2016 - Posted by Admin</span><span class="post-comments"><svg width="14" height="12" viewBox="0 0 14 12"><path d="M1 1h8v6H4l-3 2z" fill="none" stroke="#00a990" stroke-width="1.3"/><path d="M10 4h3v6l-2-1.5H6V8" fill="none" stroke="#00a990" stroke-width="1.3"/></svg>05</span></div>
    <p class="post-excerpt">Sed ut perspiciatis unde omnis iste natus error sit voluptatem accusantium doloremque laudantium, totam rem aperiam, eaque ipsa quae ab illo inventore veritatis et quasi architecto beatae vitae dicta sunt explicabo. Nemo enim ipsam voluptatem quia voluptas sit aspernatur aut odit aut fugit, sed quia consequuntur magni dolores eos qui sequi nesciunt.</p>
    <div class="post-actions"><a class="read-more" href="#">Read More</a><span class="share">&lt; Share It</span></div>
  </div>
</article>

<article class="post abs" style="top:1662px">
  <div class="post-media" role="img" aria-label="Photo of an older couple preparing vegetables together" style="background:linear-gradient(90deg,#dcdcdc,#f0ecec 35%,#e6c9d3 55%,#f4f4f4)"></div>
  <div class="post-body">
    <h3 class="post-title">On the other hand, we denounce with righteous</h3>
    <div class="post-meta"><span>21 Sep 2016 - Posted by Admin</span><span class="post-comments"><svg width="14" height="12" viewBox="0 0 14 12"><path d="M1 1h8v6H4l-3 2z" fill="none" stroke="#00a990" stroke-width="1.3"/><path d="M10 4h3v6l-2-1.5H6V8" fill="none" stroke="#00a990" stroke-width="1.3"/></svg>05</span></div>
    <p class="post-excerpt">Sed ut perspiciatis unde omnis iste natus error sit voluptatem accusantium doloremque laudantium, totam rem aperiam, eaque ipsa quae ab illo inventore veritatis et quasi architecto beatae vitae dicta sunt explicabo. Nemo enim ipsam voluptatem quia voluptas sit aspernatur aut odit aut fugit, sed quia consequuntur magni dolores eos qui sequi nesciunt.</p>
    <div class="post-actions"><a class="read-more" href="#">Read More</a><span class="share">&lt; Share It</span></div>
  </div>
</article>

<nav class="pagination abs">
  <span class="pg-btn">‹ Previous</span><span class="pg-gap"></span>
  <span class="pg-num on">1</span><span class="pg-num">2</span><span class="pg-num">3</span><span class="pg-num">4</span><span class="pg-num">5</span>
  <span class="pg-gap"></span><span class="pg-btn">Next ›</span>
</nav>

<aside>
  <div class="search-box abs">Search Blog...<svg width="14" height="14" viewBox="0 0 14 14"><circle cx="6" cy="6" r="4.5" fill="none" stroke="#333" stroke-width="1.6"/><path d="M9.3 9.3L13 13" stroke="#333" stroke-width="1.8"/></svg></div>

  <section class="widget abs" style="top:747px;height:236px">
    <h3>Categories</h3>
    <ul>
      <li>⟶ Lorem Ipsum&nbsp; dummy</li>
      <li>⟶ Lorem Ipsum is simply</li>
      <li>⟶ Lorem Ipsum is simply dummy</li>
      <li>⟶ Lorem Ipsum</li>
      <li>⟶ Lorem Ipsum is simply</li>
    </ul>
  </section>

  <section class="widget abs" style="top:1013px;height:296px">
    <h3>Recent Post</h3>
    <div class="recent"><div class="recent-thumb" role="img" aria-label="Photo of a happy family outdoors" style="background:linear-gradient(135deg,#9cc3d8,#e0b49a)"></div><div><b>At vero eos et accusamus</b><small>21 Sep 2016 - Posted by Admin</small><span><svg width="14" height="12" viewBox="0 0 14 12"><path d="M1 1h8v6H4l-3 2z" fill="none" stroke="#00a990" stroke-width="1.3"/><path d="M10 4h3v6l-2-1.5H6V8" fill="none" stroke="#00a990" stroke-width="1.3"/></svg>08</span></div></div>
    <div class="recent"><div class="recent-thumb" role="img" aria-label="Photo of a couple relaxing at the beach" style="background:linear-gradient(135deg,#7fb9e0,#e8c9a0)"></div><div><b>But I must explain to you</b><small>20 Sep 2016 - Posted by Admin</small><span><svg width="14" height="12" viewBox="0 0 14 12"><path d="M1 1h8v6H4l-3 2z" fill="none" stroke="#00a990" stroke-width="1.3"/><path d="M10 4h3v6l-2-1.5H6V8" fill="none" stroke="#00a990" stroke-width="1.3"/></svg>5</span></div></div>
    <div class="recent"><div class="recent-thumb" role="img" aria-label="Photo of a woman holding fresh vegetables" style="background:linear-gradient(135deg,#d9603a,#9bbb5a)"></div><div><b>On the other hand</b><small>19 Sep 2016 - Posted by Admin</small><span><svg width="14" height="12" viewBox="0 0 14 12"><path d="M1 1h8v6H4l-3 2z" fill="none" stroke="#00a990" stroke-width="1.3"/><path d="M10 4h3v6l-2-1.5H6V8" fill="none" stroke="#00a990" stroke-width="1.3"/></svg>15</span></div></div>
  </section>

  <section class="widget abs" style="top:1341px;height:237px">
    <h3>Archives</h3>
    <ul>
      <li>⟶ September 2016</li><li>⟶ August 2016</li><li>⟶ July 2016</li><li>⟶ June 2016</li><li>⟶ May 2016</li>
    </ul>
  </section>

  <section class="widget abs" style="top:1609px;height:194px">
    <h3>Tags</h3>
    <p class="tags">Sed <b>Verdia</b> perspiciatis unde omnis iste natus error sit voluptatem <b>Verdia</b> doloremque laudantium, <b>HEALTHY MEALS</b> rem aperiam, eaque <b>ipsa</b> quae ab illo inventore veritatis</p>
  </section>
</aside>

<footer class="site-footer abs">
  <div class="f-col quick abs" style="left:161px;width:122px">
    <h4>Quick <em>Links</em></h4>
    <ul>
      <li class="on">Home</li><li>About VitaPath</li><li>Our Courses</li><li>Special Offers</li><li>Testimonials</li><li>Blog</li><li>Faq's</li><li>Contact Us</li>
    </ul>
  </div>
  <div class="f-col contact abs" style="left:326px;width:220px">
    <h4>Contact <em>Details</em></h4>
    <p class="firm">VitaPath For Wellness</p>
    <p>48 Willowmere Lane, Suite 210,<br>Brookfield Park - 604 219</p>
    <div class="row"><svg width="14" height="14" viewBox="0 0 24 24"><path fill="#00a990" d="M6.6 10.8a15 15 0 0 0 6.6 6.6l2.2-2.2c.3-.3.7-.4 1-.2 1.1.4 2.3.6 3.6.6.6 0 1 .4 1 1V20c0 .6-.4 1-1 1A17 17 0 0 1 3 4c0-.6.4-1 1-1h3.5c.6 0 1 .4 1 1 0 1.3.2 2.5.6 3.6.1.3 0 .7-.2 1z"/></svg>555-310-2847</div>
    <div class="row"><svg width="16" height="14" viewBox="0 0 16 14"><rect x="1" y="5" width="14" height="7" fill="#00a990"/><rect x="4" y="1" width="8" height="4" fill="none" stroke="#00a990" stroke-width="1.4"/></svg>555-310-2911</div>
    <div class="row small"><svg width="15" height="11" viewBox="0 0 15 11"><rect width="15" height="11" fill="#00a990"/><path d="M0 0l7.5 6L15 0" fill="none" stroke="#1e2430" stroke-width="1.2"/></svg>hello@vitapathwellness.example</div>
  </div>
  <div class="f-col follow abs" style="left:567px;width:225px">
    <h4>Follow <em>Us</em></h4>
    <ul>
      <li><i style="background:#3b5998"></i>Friendpage</li>
      <li><i style="background:#4bb0e0"></i>Chirpline</li>
      <li><i style="background:#1a75b0"></i>Workmesh</li>
      <li><i style="background:#d8342a"></i>Circleplus</li>
    </ul>
  </div>
  <div class="footer-brand abs"><span></span>VitaPath</div>
</footer>

<div class="copyright abs">© 2016 VitaPath For Wellness. All Rights Reserved.</div>

</body>
</html>
```